I would like a business card to match my truck wrap and logo. I would like the font to match my existing business card please.

Industry/Entity Type

Painter

Contact Information for Business Card

Rodrigo Fenwar 801-437-2190 Fenwarcoatings.utah@brelmox.com
SERVICES - Custom Paint & Stain, Interior & Exterior, Epoxy Coatings / Garage Floors, Cabinet Refinishing, Log Staining and Refinishing.

Requirements
Nice to have
• I would like to have the white and grey line like the bottom of my vehicle wrap, Light Grey to match my truck also.

```html
<!DOCTYPE html>
<html lang="en">
<head>
<meta charset="utf-8">
<title>Fenwar Coatings – Business Card</title>
<link href="https://fonts.googleapis.com/css2?family=Arimo:wght@400;700&family=Saira:wght@700&display=swap" rel="stylesheet">
<style>
  :root {
    --backdrop: #9c9c9c;
    --truck-grey: #aeb5c2;
    --paper: #ffffff;
    --brand-blue: #00a8ec;
    --blue-top: #00aeef;
    --blue-bottom: #0d5c99;
    --ink-blue: #1670b4;
  }
  * { margin: 0; padding: 0; box-sizing: border-box; }
  html, body { width: 1200px; height: 1200px; overflow: hidden; }
  body { background: var(--backdrop); position: relative; font-family: "Arimo", Arial, sans-serif; }

  .card {
    position: absolute; top: 303px; width: 368px; height: 594px;
    background: var(--paper); overflow: hidden;
  }
  .card--front { left: 201px; }
  .card--back { left: 597px; }

  .band { position: absolute; left: 0; width: 100%; }

  /* brand block */
  .brand { position: absolute; left: 0; width: 100%; text-align: center; }
  .brand__square { width: 62px; height: 62px; margin: 0 auto 58px; }
  .brand__name {
    font-family: "Arimo", Arial, sans-serif; font-weight: 700;
    line-height: 1; text-transform: uppercase;
  }
  .brand__name .line1 { display: block; font-size: 46px; letter-spacing: 2px; }
  .brand__name .line2 { display: block; font-size: 19px; letter-spacing: 11px; margin-top: 10px; padding-left: 11px; }

  .card--front .brand { top: 78px; }
  .card--front .brand__square { background: var(--paper); }
  .card--front .brand__name { color: var(--paper); }

  .card--back .brand { top: 88px; }
  .card--back .brand__square { background: var(--brand-blue); }
  .card--back .brand__name { color: var(--brand-blue); }

  /* services */
  .services {
    position: absolute; top: 359px; left: 0; width: 100%; height: 211px;
    background: linear-gradient(to bottom, var(--blue-top), var(--blue-bottom));
    color: var(--paper); padding: 10px 0 0 29px;
  }
  .services__title { font-weight: 700; font-size: 19px; margin-bottom: 8px; }
  .services__list { list-style: none; }
  .services__item { font-size: 19px; height: 31.4px; display: flex; align-items: center; }
  .services__item::before {
    content: ""; width: 9px; height: 9px; background: var(--paper);
    transform: rotate(45deg); margin: 0 9px 4px 2px; flex: none;
  }

  /* contact */
  .contact {
    position: absolute; top: 428px; left: 0; width: 100%; text-align: center;
    font-family: "Saira", "Arial Narrow", sans-serif; font-weight: 700; color: var(--ink-blue);
  }
  .contact__name { font-size: 21px; text-transform: uppercase; line-height: 1; }
  .contact__rule { width: 124px; height: 1px; background: #d6dae2; margin: 10px auto 12px; }
  .contact__phone { font-size: 20px; line-height: 1.15; letter-spacing: 0.5px; }
  .contact__email { font-size: 16px; line-height: 1.35; }
</style>
</head>
<body>

<section class="card card--front">
  <div class="band" style="top:0;height:349px;background:var(--truck-grey)"></div>
  <div class="brand">
    <div class="brand__square"></div>
    <div class="brand__name"><span class="line1">Fenwar</span><span class="line2">Coatings</span></div>
  </div>
  <div class="services">
    <h2 class="services__title">SERVICES</h2>
    <ul class="services__list">
      <li class="services__item">Custom Paint &amp; Stain</li>
      <li class="services__item">Interior &amp; Exterior</li>
      <li class="services__item">Epoxy Coatings / Garage Floors</li>
      <li class="services__item">Cabinet Refinishing</li>
      <li class="services__item">Log Staining and Refinishing.</li>
    </ul>
  </div>
  <div class="band" style="top:579px;height:15px;background:var(--truck-grey)"></div>
</section>

<section class="card card--back">
  <div class="brand">
    <div class="brand__square"></div>
    <div class="brand__name"><span class="line1">Fenwar</span><span class="line2">Coatings</span></div>
  </div>
  <div class="band" style="top:360px;height:12px;background:var(--truck-grey)"></div>
  <div class="band" style="top:381px;height:188px;background:var(--truck-grey)"></div>
  <div class="band" style="top:577px;height:17px;background:var(--truck-grey)"></div>
  <div class="contact">
    <p class="contact__name">Rodrigo Fenwar</p>
    <div class="contact__rule"></div>
    <p class="contact__phone">801-437-2190</p>
    <p class="contact__email">Fenwarcoatings.utah@brelmox.com</p>
  </div>
</section>

</body>
</html>
```